New webdesign for a cable company

We need a new design for Lunor Media.

There exist a suggestion for the page, were we have attached files to show you this. The design here is not good enough, but here you can se what content we need.

You can feel free to give adjustment to this design to make it better, our blow us away with a new brilliant design, but from this design you see what content we need.

The important is that the company get a design who represent its products:
- TV = Cable TV
- Bredbånd = Broadband
- Mobil = Mobile phone
- Strøm = Electricity
- Alarm = Alarm
- Lunor Komplett = a cobain pagage of all our products.

Lunor Media would like costumers who visit the site to het the impression that Lunor Media is a professional, innovative and fun company.
Updates

We have to day uploaded pictures of the existing page as the link haven't been working for the most of you as it's placed on a server our developer are using and is often shut it down. 

We have also updated the brief with some new and updated description so please read true the updated brief. 

We will at the same time inform that we haven't been able to give feedback on any of the received design and are sorry for that, we will within the next 24 hours hopefully have started responded the different received designs.

Looking forward to see more suggestion and hope you will help us create and very professional and informative design. 

Reason: We have decided to extend the deadline due to the number of design suggestion who is sent in and your lack of response to all designers due to our own workload.

This project was unfortunately for different reason put on ice for a while, but we are now ready to complete the design and will answer and give feedback too all the received design suggestions. 

Within a couple of days we hope we have answered all you who sent us suggestions, we appreciate all suggestions and hope to get in more suggestions.

Reason: Deisgn description have been updated

Target Market(s)

Our costumer are both private and companies

Industry/Entity Type

Tv

Requirements
Must have
• A easy way to promote and inform about changes in our products, there are a constant change in our products and it must bee a easy and good way to changes ass the marked change. Cheek out this link, for a example of what we like/think of here, https://nett.fjordsignal.no

On all pages there must be a easy way to click on a order button and too inform about your interest (thats two different things), could be placed in the top right corner for example. In the order form you should follow a step by step part:
1. Cheek what product we can provide you.
2. Chooce products.
3. Costumer inforamtion.
4. Confirmation.

Somewere on the portal it must be possible for costumers to log on to their own administration, where they can cheek for invoices, other statuses, etc.

A main menu existing of:
Hjem (Home)
Produkter (Products)
Storkunde (key account/large costumers)
Kundeservice (Costumerservice)
Min side (My page)

The main menu should have the following sub titles:
- Under "Produkter"/products our different products must be listed
- Under "Kundeservice"/Costumerservice it must have these submenus:
- Hjelp og støtte = Help.
- Faktura = Invoice
- Brukerguider = Userguides
- Abbonementavtaler = Terms and conditions.

A bottom menu where we have 5 main categories, with sub categories:
Om oss (about us)
- Om Lunor Media (about Lunor Media)
- Kontaktinformajson ( contact information)
- Pressemeldinger (Pressrelese)
- Ledige stillinger (positions available)
- KRAV ( and organisastion in our field)

Produkter (Product)
- TV (TV)
- Bredbånd (Broadand)
- Telefoni (telephony, both mobil)
- Strøm (elecricity)
- Arlam (Alarm)

Borrettslag/Sameier (Housing cooperatives)
- Løsninger (solutions)
- Produkter (product)
- Kontaktpersoner (contactpersons)

Utbygger (developer)
- Hva vi kan gjøre for dere. (What we can do for you)

Opperatørnett (operators)

Build up the categories and bottom menu something like this:
https://nett.fjordsignal.no
www.brevix.com
Nice to have
• A main menu existing of:
Hjem (Home)
Produkter (Products)
Lunor Media
Kontakt oss (Contact us)

Under "Produkter"/products our different products must be listed and under "Kundeservice"/Costumerservice it must have these submenus:
- Hjelp og støtte = Help.
- Faktura = Invoice
Should not have
• Any translation section since the homepage only will be in Norwegian.

```html
<!DOCTYPE html>
<html lang="no">
<head>
<meta charset="utf-8">
<title>Lunor Media</title>
<link href="https://fonts.googleapis.com/css2?family=Roboto:wght@100;300;400;500&display=swap" rel="stylesheet">
<style>
:root{
  --brand:#3cc3ef;
  --brand-dark:#1fa9dc;
  --ink:#444;
  --ink-soft:#666;
  --white:#fff;
  --footer-base:#5c5c5c;
}
*{margin:0;padding:0;box-sizing:border-box}
html,body{width:1200px;height:1073px;overflow:hidden}
body{position:relative;background:var(--white);font-family:"Roboto",Arial,sans-serif;color:var(--ink)}
a{color:inherit;text-decoration:none}
.abs{position:absolute}

/* top bar */
.topbar{left:0;top:0;width:1200px;height:38px;background:var(--brand)}
.audience{left:200px;top:12px;display:flex;font-size:10.5px;color:var(--white)}
.audience a{padding:0 10px;border-left:1px solid rgba(255,255,255,.6)}
.audience a:first-child{padding-left:0;border-left:0}
.social{display:flex;gap:6px}
.social span{width:20px;height:20px;border-radius:50%;background:var(--white);display:block}
.top-social{left:662px;top:9px}
.search{left:765px;top:8px;width:140px;height:22px;background:var(--white);font-size:10px;color:#999;padding:6px 5px}
.search svg{position:absolute;right:3px;top:3px}
.login{left:913px;top:8px;width:87px;height:22px;border:1px solid var(--white);color:var(--white);font-size:10.5px;display:flex;align-items:center;justify-content:center;gap:5px}

/* header */
.header{left:0;top:46px;width:1200px;height:58px;background:var(--white);border-top:1px solid #e5e5e5}
.logo{left:200px;top:14px;display:flex;align-items:center;gap:10px;font-size:30px;font-weight:400;color:var(--brand)}
.logo i{width:22px;height:22px;border-radius:50%;background:var(--brand);display:block}
.nav{right:200px;top:20px;display:flex;font-size:14px;color:#333}
.nav a{padding:0 18px;border-left:1px dotted #999}
.nav a:first-child{border-left:0}
.nav a:last-child{padding-right:0}
.nav a.current{color:var(--brand)}

/* hero */
.hero{left:0;top:104px;width:1200px;height:393px;background:linear-gradient(#e9e9e9,#f5f5f5 60%,#eaeaea)}
.ring{left:232px;top:130px;font-size:24px;font-weight:300;color:#444}
.phone-big{left:480px;top:120px;display:flex;align-items:center;gap:6px;font-size:50px;font-weight:100;color:#555;line-height:1}
.cta{left:840px;top:118px;display:flex;flex-direction:column;gap:6px;width:160px}
.cta a{height:26px;display:flex;align-items:center;justify-content:center;font-size:12px}
.cta .order{background:var(--brand);color:var(--white)}
.cta .interest{border:1px solid var(--brand);color:var(--brand-dark);background:var(--white)}
.hero-art{left:203px;top:186px;width:797px;height:296px;background:linear-gradient(90deg,#cdeefb,#8fdaf5 45%,#d6f1fb 70%,#b6e6f8)}

/* content */
.welcome{left:199px;top:500px;font-size:42px;font-weight:100;color:#555}
.welcome b{font-weight:300;color:var(--brand)}
.welcome em{font-style:normal;font-weight:300;color:#444}
.intro{left:199px;top:561px;width:802px;font-size:10.2px;line-height:17.6px;color:var(--ink-soft);letter-spacing:.1px}

.col h2{font-size:24px;font-weight:300;color:var(--brand);line-height:1}
.col p{font-size:10px;line-height:12.5px;color:var(--ink-soft)}
.services{left:199px;top:684px;width:245px}
.services p{margin-top:5px}
.services ul{list-style:none;margin-top:8px;font-size:11px;color:#333}
.services li{display:flex;align-items:center;gap:9px;height:16px}
.services li::before{content:"";border-left:9px solid var(--brand);border-top:5px solid transparent;border-bottom:5px solid transparent}
.btn{display:inline-block;margin-top:8px;background:var(--brand);color:var(--white);font-size:11px;padding:4px 9px}
.divider{top:682px;height:194px;border-left:1px dotted #bbb}
.stories{left:500px;top:684px;width:220px}
.story{display:flex;gap:4px;margin-top:9px}
.story .thumb{width:49px;height:47px;background:#a9a9a9;flex:none;display:flex;align-items:center;justify-content:center}
.story .thumb i{width:22px;height:22px;border-radius:50%;background:var(--brand);display:block}
.story + .story{margin-top:22px}
.story a{display:block;text-align:center;font-size:11px;color:var(--brand);margin-top:2px}
.news{left:788px;top:684px;width:212px}
.event{display:flex;gap:12px;margin-top:13px;align-items:flex-start}
.event + .event{margin-top:24px}
.date{width:29px;height:29px;border:2px solid #666;font-size:9px;line-height:10px;text-align:center;padding-top:3px;color:#444;flex:none}
.event p{margin-top:3px}

/* footer */
.footer{left:0;top:916px;width:1200px;height:116px;background:var(--brand);color:var(--white)}
.fcol{color:var(--white)}
.fcol h3{font-size:12.5px;font-weight:400;text-decoration:underline;margin-bottom:6px}
.fcol a{display:block;font-size:10.5px;font-weight:300;line-height:15px}
.f-about{left:200px;top:924px}
.f-products{left:322px;top:924px}
.f-housing{left:408px;top:924px}
.f-developer{left:530px;top:924px;width:110px}
.f-operators{left:650px;top:924px}
.f-operators .label{margin-top:16px;font-size:10.5px;font-weight:400}
.f-operators .hours{margin-top:2px;font-size:15px;font-weight:100;line-height:1}
.f-operators .num{font-size:21px;font-weight:100;line-height:1.1}
.footer-social{left:904px;top:926px}
.newsletter{left:805px;top:972px}
.newsletter h3{font-size:18px;font-weight:300;letter-spacing:-.5px;color:#333}
.signup{margin-top:2px;width:195px;height:25px;background:var(--white);border:1px solid var(--white);display:flex;justify-content:space-between;align-items:center;padding-left:6px;font-size:11px;color:#777}
.signup span{background:var(--brand);color:var(--white);height:21px;padding:3px 10px;margin-right:1px;font-size:12px}
.base{left:0;top:1032px;width:1200px;height:41px;background:var(--footer-base)}
.copy{left:202px;top:1046px;font-size:10px;font-weight:300;color:#eee}
.base-logo{right:200px;top:1041px;display:flex;align-items:center;gap:8px;font-size:19px;color:var(--white)}
.base-logo i{width:16px;height:16px;border-radius:50%;background:var(--white);display:block}
</style>
</head>
<body>
<div class="abs topbar"></div>
<nav class="abs audience"><a href="#">Private Customer</a><a href="#">Housing Associations</a><a href="#">RealEstate Developer</a><a href="#">Business Customer</a></nav>
<div class="abs social top-social"><span></span><span></span><span></span><span></span></div>
<div class="abs search">Search...
  <svg width="16" height="16" viewBox="0 0 16 16"><circle cx="6.5" cy="6.5" r="4.5" fill="none" stroke="#555" stroke-width="2"/><line x1="10" y1="10" x2="14" y2="14" stroke="#555" stroke-width="2.5"/></svg>
</div>
<a class="abs login" href="#">
  <svg width="10" height="11" viewBox="0 0 10 11"><circle cx="5" cy="3" r="2.5" fill="#fff"/><path d="M0 11 Q0 6 5 6 Q10 6 10 11 Z" fill="#fff"/></svg>
  Logg inn
</a>

<header class="abs header">
  <div class="abs logo"><i></i>Lunor Media</div>
  <nav class="abs nav"><a class="current" href="#">Hjem</a><a href="#">Produkter</a><a href="#">Storkunde</a><a href="#">Kundeservice</a><a href="#">Min side</a></nav>
</header>

<section class="abs hero"></section>
<div class="abs ring">Ring Us: 10:00 - 15:00</div>
<div class="abs phone-big">
  <svg width="40" height="46" viewBox="0 0 44 50"><path d="M8 2 L16 12 L12 18 Q16 30 28 38 L34 34 L42 42 L36 48 Q20 48 8 32 Q0 18 2 8 Z" fill="var(--brand)"/></svg>
  47 21 38 90
</div>
<div class="abs cta"><a class="order" href="#">Bestill</a><a class="interest" href="#">Meld interesse</a></div>
<div class="abs hero-art" role="img" aria-label="Hand reaching toward a blue globe among glowing hexagonal network shapes"></div>

<h1 class="abs welcome">Welcome to <b>Lunor</b> <em>Media</em></h1>
<p class="abs intro">Lorem ipsum dolor sit amet, consectetur adipiscing elit. Praesent adipiscing auctor tortor at viverra. Nam pellentesque est ac dolor dapibus ac venenatis ipsum aliquet. Sed adipiscing faucibus felis, vel porta velit volutpat ut. Aliquam erat volutpat. Mauris aliquet, nibh ac laoreet consectetur, nisi risus malesuada mi, vitae imperdiet quam lorem a neque. Nam sapien urna, dictum blandit viverra vel, aliquam non lacus. Praesent pretium nulla at orci gravida id posuere felis porttitor. Lorem ipsum dolor sit amet, consectetur adipiscing elit. Pellentesque laoreet tristique nulla, ut faucibus tortor mattis a. Curabitur eu odio lorem, a molestie arcu. Sed in massa sed tortor pretium rhoncus. Curabitur condimentum fringilla laoreet. Integer varius felis faucibus purus adipiscing cursus.</p>

<section class="abs col services">
  <h2>Services</h2>
  <p>Lorem ipsum dolor sit amet, consectetur adipiscing elit. Praesent adipiscing auctor tortor at viverra. Nam pellentesque est ac dolor dapibus ac imandfe venenatis ipsum aliquet.</p>
  <ul><li>Broadband</li><li>Cabel TV</li><li>Mobile Phone</li><li>Electricity</li><li>Alarm</li><li>Lunor Komplett</li></ul>
  <a class="btn" href="#">More...</a>
</section>
<div class="abs divider" style="left:467px"></div>
<section class="abs col stories">
  <h2>Success Stories</h2>
  <div class="story"><div class="thumb"><i></i></div><div><p>Lorem ipsum dolor sit amet, consectetur adipiscing elit. Praese adipiscing auctor tortor at viverra. Nam pellentesque est ac dolor</p><a href="#">Lunor Media</a></div></div>
  <div class="story"><div class="thumb"><i></i></div><div><p>Lorem ipsum dolor sit amet, consectetur adipiscing elit. Praese adipiscing auctor tortor at viverra. Nam pellentesque est ac dolor</p><a href="#">Lunor Media</a></div></div>
</section>
<div class="abs divider" style="left:748px"></div>
<section class="abs col news">
  <h2>News &amp; Events</h2>
  <div class="event"><div class="date">10<br>May</div><p>Lorem ipsum dolor sit amet,<br>consectetur adipiscing elit.</p></div>
  <div class="event"><div class="date">10<br>May</div><p>Lorem ipsum dolor sit amet,<br>consectetur adipiscing elit.</p></div>
  <div class="event"><div class="date">10<br>May</div><p>Lorem ipsum dolor sit amet,<br>consectetur adipiscing elit.</p></div>
</section>

<footer class="abs footer"></footer>
<div class="abs fcol f-about"><h3>Om oss</h3><a href="#">Om Lunor Media</a><a href="#">Kontaktinformasjon</a><a href="#">Pressemeldinger</a><a href="#">Ledige stillinger</a><a href="#">KRAV</a></div>
<div class="abs fcol f-products"><h3>Produkter</h3><a href="#">TV</a><a href="#">Bredbånd</a><a href="#">Telefoni</a><a href="#">Strøm</a><a href="#">Alarm</a></div>
<div class="abs fcol f-housing"><h3>Borrettslag/Sameier</h3><a href="#">Løsninger</a><a href="#">Produkter</a><a href="#">Kontaktpersoner</a></div>
<div class="abs fcol f-developer"><h3>Utbygger</h3><a href="#">Hva vi kan gjøre for dere</a></div>
<div class="abs fcol f-operators"><h3>Operatørnett</h3><div class="label">Kontakt oss:</div><div class="hours">10:00 - 15:00</div><div class="num">47 21 38 90</div></div>
<div class="abs social footer-social"><span></span><span></span><span></span><span></span></div>
<div class="abs newsletter"><h3>NEWSLETTER</h3><div class="signup">Email Address<span>Sign Up</span></div></div>
<div class="abs base"></div>
<div class="abs copy">Copyright © Lunor Media AS - 2013. All rights reserved.</div>
<div class="abs base-logo"><i></i>Lunor Media</div>
</body>
</html>
```